Business Card Design

We need a business card design for a Dry cleaners in Brisbane, Australia. We are trying to promote a fresh/clean image consistent with our website. www.pinnelgarmentcare.com.au

Looking for a professional neat card that's easy to read.

Target Market(s)

Customers looking for a professional, fresh and clean drycleaners.

Industry/Entity Type

Business

Contact Information for Business Card

See our existing business card. The Fax number (07) 3468 5270 to be removed.

Requirements
Must have
• All the details on current business card less the fax number.
Nice to have
• I like white text on coloured background. Blue works well as we are located near the water...

```html
<!DOCTYPE html>
<html lang="en">
<head>
<meta charset="utf-8">
<title>Pinnel Garment Care – Business Card</title>
<link rel="stylesheet" href="https://fonts.googleapis.com/css2?family=PT+Sans:wght@400;700&display=swap">
<style>
  :root {
    --backdrop: #3b3b3b;
    --white: #ffffff;
    --brand-blue: #27a6df;
    --sky: #1fa9e4;
    --mid-blue: #1a74c4;
    --deep-blue: #2a2f86;
  }
  * { margin: 0; padding: 0; box-sizing: border-box; }
  html, body {
    width: 1200px;
    height: 999px;
    overflow: hidden;
    background: var(--backdrop);
    font-family: "PT Sans", sans-serif;
  }
  .card {
    position: absolute;
    left: 75px;
    top: 199px;
    width: 1050px;
    height: 600px;
    overflow: hidden;
    background: radial-gradient(ellipse 560px 440px at 580px 340px, var(--sky) 0%, var(--mid-blue) 55%, var(--deep-blue) 100%);
  }
  .card-shapes { position: absolute; inset: 0; }
  .brand-name {
    position: absolute;
    left: 50px;
    top: 180px;
    width: 470px;
    text-align: center;
    color: var(--brand-blue);
    font-weight: 700;
    font-size: 46px;
    line-height: 1.1;
  }
  .contact { position: absolute; inset: 0; color: var(--white); }
  .person-name {
    position: absolute;
    left: 595px;
    top: 226px;
    font-size: 45px;
    white-space: nowrap;
  }
  .detail {
    position: absolute;
    left: 639px;
    font-size: 26px;
    line-height: 35px;
    white-space: nowrap;
  }
  .detail-address { top: 314px; }
  .detail-phone { top: 407px; }
  .detail-mobile { top: 442px; }
  .detail-email { top: 477px; }
  .icon { position: absolute; left: 590px; width: 26px; height: 26px; }
  .icon-pin { top: 318px; }
  .icon-phone { top: 412px; }
  .icon-mobile { top: 447px; }
  .icon-email { top: 482px; }
  .locations {
    position: absolute;
    left: 396px;
    top: 536px;
    font-size: 35px;
    white-space: nowrap;
  }
  .locations .sep { margin: 0 38px; }
</style>
</head>
<body>
  <div class="card">
    <svg class="card-shapes" width="1050" height="600" viewBox="0 0 1050 600" aria-hidden="true">
      <defs>
        <clipPath id="upper-area">
          <rect x="0" y="0" width="1050" height="538"/>
        </clipPath>
        <linearGradient id="panel-fade" x1="0" y1="0" x2="0" y2="1">
          <stop offset="0" stop-color="#eceef1"/>
          <stop offset="0.15" stop-color="#ffffff"/>
          <stop offset="1" stop-color="#ffffff"/>
        </linearGradient>
        <linearGradient id="swoosh-fade" x1="0" y1="0" x2="0" y2="1">
          <stop offset="0" stop-color="#ffffff" stop-opacity="0"/>
          <stop offset="0.45" stop-color="#d6eefb" stop-opacity="0.95"/>
          <stop offset="1" stop-color="#ffffff" stop-opacity="0"/>
        </linearGradient>
      </defs>
      <ellipse cx="150" cy="120" rx="442" ry="430" fill="url(#panel-fade)" clip-path="url(#upper-area)"/>
      <path d="M 556 235 Q 500 380 398 446" fill="none" stroke="url(#swoosh-fade)" stroke-width="8" stroke-linecap="round"/>
    </svg>

    <div class="brand-name">Pinnel Garment Care</div>

    <div class="contact">
      <div class="person-name">Jordan Pell</div>

      <svg class="icon icon-pin" viewBox="0 0 24 24" aria-hidden="true">
        <path d="M12 1.5c-4.2 0-7.5 3.3-7.5 7.4 0 5.5 7.5 14 7.5 14s7.5-8.5 7.5-14c0-4.1-3.3-7.4-7.5-7.4zm0 10.3a2.9 2.9 0 1 1 0-5.8 2.9 2.9 0 0 1 0 5.8z" fill="#fff"/>
      </svg>
      <div class="detail detail-address">27 Kestrel Rd<br>Elmsby Qld 4182</div>

      <svg class="icon icon-phone" viewBox="0 0 24 24" aria-hidden="true">
        <path d="M6.6 3.5l2.6 3.4-1.6 2.2c1 2.2 2.9 4.2 5.2 5.3l2.2-1.6 3.4 2.6-1.3 3c-7.4-.4-13.1-6.1-13.5-13.5z" fill="none" stroke="#fff" stroke-width="2" stroke-linejoin="round"/>
        <path d="M14 4a6 6 0 0 1 6 6M14 7.5a2.6 2.6 0 0 1 2.6 2.6" fill="none" stroke="#fff" stroke-width="1.8" stroke-linecap="round"/>
      </svg>
      <div class="detail detail-phone">(07) 3520 4418</div>

      <svg class="icon icon-mobile" viewBox="0 0 24 24" aria-hidden="true">
        <rect x="2" y="2" width="20" height="20" rx="4" fill="#fff"/>
        <rect x="7" y="5" width="10" height="14" rx="1.5" fill="none" stroke="#1d6fc0" stroke-width="1.8"/>
        <path d="M9 15l6-6" stroke="#1d6fc0" stroke-width="1.5"/>
      </svg>
      <div class="detail detail-mobile">0400 512 786</div>

      <svg class="icon icon-email" viewBox="0 0 24 24" aria-hidden="true">
        <rect x="2" y="2" width="20" height="20" rx="4" fill="#fff"/>
        <circle cx="12" cy="12" r="2.8" fill="none" stroke="#1d6fc0" stroke-width="1.7"/>
        <path d="M14.8 10v3c0 1.3 2.6 1.6 2.6-1a5.4 5.4 0 1 0-2.3 4.4" fill="none" stroke="#1d6fc0" stroke-width="1.7" stroke-linecap="round"/>
      </svg>
      <div class="detail detail-email">jo@pinnelgarmentcare.com.au</div>

      <div class="locations">Elmsby<span class="sep">|</span>Larkfield<span class="sep">|</span>Calloway Pt</div>
    </div>
  </div>
</body>
</html>
```